Young, modern, highly skilled carpenter needs business card design

I need a business card design for my construction business. Its called 'Barlow Construction Services'. Im looking for a ultra modern design that incorporates B C S, the first letters of the name with only a subtle reference to carpentry. The design should reflect my high quality work and eye for detail. i have also uploaded some exmaple designs i like.

Industry/Entity Type

Construction

Requirements
Must have
• Name of business, my name, mobile number, ABN number, email address
Nice to have
• A logo incorporating the name of the business

```html
<!DOCTYPE html>
<html lang="en">
<head>
<meta charset="UTF-8">
<title>Barlow Construction Services – Business Card</title>
<link rel="stylesheet" href="https://fonts.googleapis.com/css2?family=Ubuntu:wght@400;700&display=swap">
<style>
  :root {
    --backdrop: #7e8f8f;
    --brand-green: #52ff00;
    --ink: #1d1d1b;
    --paper: #ffffff;
  }
  html, body {
    margin: 0;
    padding: 0;
    width: 1200px;
    height: 900px;
    overflow: hidden;
    background: var(--backdrop);
    font-family: "Ubuntu", sans-serif;
  }
  .canvas {
    position: relative;
    width: 1200px;
    height: 900px;
  }
  .card {
    position: absolute;
    left: 336px;
    width: 541px;
    height: 372px;
  }
  .card-front {
    top: 60px;
    background: var(--brand-green);
  }
  .card-back {
    top: 460px;
    height: 370px;
    background: var(--paper);
  }
  .wordmark {
    position: absolute;
    margin: 0;
    font-weight: 700;
    line-height: 1;
    letter-spacing: 4px;
  }
  .card-front .wordmark {
    left: 0;
    right: 0;
    top: 168px;
    text-align: center;
    font-size: 62px;
    color: var(--ink);
  }
  .contact {
    position: absolute;
    left: 66px;
    top: 50px;
    margin: 0;
    font-size: 19px;
    line-height: 26.5px;
    color: var(--ink);
    font-style: normal;
  }
  .contact-name {
    display: block;
    color: var(--brand-green);
    font-size: 20px;
  }
  .card-back .wordmark {
    right: 69px;
    top: 252px;
    font-size: 40px;
    color: var(--brand-green);
  }
  .business-name {
    position: absolute;
    right: 68px;
    top: 294px;
    margin: 0;
    font-weight: 700;
    font-size: 20.5px;
    color: var(--ink);
    white-space: nowrap;
  }
</style>
</head>
<body>
  <main class="canvas">
    <section class="card card-front" aria-label="Card front">
      <p class="wordmark">BCS</p>
    </section>

    <section class="card card-back" aria-label="Card back">
      <address class="contact">
        <span class="contact-name">Liam Barlow</span>
        M: liam.barlow@bcsmail.net<br>
        T: 0412558036<br>
        ABN: 41 286 507 392
      </address>
      <p class="wordmark">BCS</p>
      <p class="business-name">BARLOW CONSTRUCTION SERVICES</p>
    </section>
  </main>
</body>
</html>
```